Design Cover for Catalog and theme pages to match cover design for continuity

I need a catalog cover for our new catalog and have it flow through the pages uniting the design together. Most the hardest work is complete however it needs a designers touch to bring it all together. The attached files include the catalog with products images data and logos. We have more assets however with the 100MB limit we are unable to upload to many more. For additional images you can pull them from our website www.brovantek.example.

Target Market(s)

Tradesmen and trades women who work in the Electrical and Industrial Automation spaces.

Industry/Entity Type

Industrial

Font styles to use
Sans Serif

Colors
3176b5
0555a3
85cae6

Requirements
Must have
• Complete cover design
• Must also have cover theme flow through remaining pages
Nice to have
• Header and Footer on each page
• Index on cover with page reference
Should not have
• This is not a redesign of the whole catalog, please don't drastically change the pages or any of the data in the tables.

```html
<!DOCTYPE html>
<html lang="en">
<head>
<meta charset="utf-8">
<title>Brovantek Catalogue</title>
<link rel="stylesheet" href="https://fonts.googleapis.com/css2?family=Bebas+Neue&display=swap">
<style>
  :root {
    --blue-light: #85cae6;
    --blue-mid: #3176b5;
    --blue-deep: #0555a3;
    --navy: #2a3f8c;
    --orange: #f7931e;
    --white: #ffffff;
    --text-soft: #e6f1fb;
  }
  * { margin: 0; padding: 0; box-sizing: border-box; }
  html, body { width: 934px; height: 1200px; overflow: hidden; }
  body { font-family: "Bebas Neue", "Arial Narrow", sans-serif; }
  .cover {
    position: relative;
    width: 934px;
    height: 1200px;
    background: linear-gradient(160deg, #1d7fc6 0%, var(--blue-deep) 45%, #1f4a9c 75%, var(--navy) 100%);
    overflow: hidden;
  }
  .brand {
    position: absolute;
    top: 128px;
    left: 0;
    width: 100%;
    text-align: center;
    font-size: 104px;
    line-height: 1;
    letter-spacing: 4px;
    color: var(--blue-light);
  }
  .title {
    position: absolute;
    top: 272px;
    left: 0;
    width: 100%;
    text-align: center;
    font-size: 84px;
    line-height: 1;
    letter-spacing: 1px;
    color: var(--white);
  }
  .product-visual {
    position: absolute;
    left: 187px;
    top: 423px;
    width: 548px;
    height: 355px;
    border-radius: 24px;
    background: radial-gradient(ellipse at 50% 55%, rgba(170, 215, 245, 0.55) 0%, rgba(110, 170, 225, 0.35) 45%, rgba(49, 118, 181, 0) 75%);
  }
  .intro {
    position: absolute;
    left: 187px;
    top: 847px;
    width: 392px;
    height: 221px;
    border-top: 1px solid var(--blue-light);
    border-bottom: 1px solid var(--blue-light);
    padding-top: 12px;
  }
  .intro p {
    font-size: 15.5px;
    line-height: 21px;
    text-align: center;
    color: var(--text-soft);
    letter-spacing: 0.2px;
  }
  .index {
    position: absolute;
    left: 666px;
    top: 847px;
    width: 268px;
    list-style: none;
  }
  .index li {
    display: flex;
    justify-content: space-between;
    align-items: center;
    height: 45px;
    margin-bottom: 13.5px;
    padding: 0 16px 0 16px;
    background: var(--white);
    border-radius: 23px 0 0 23px;
    color: var(--orange);
    font-size: 22px;
    letter-spacing: 0.3px;
  }
</style>
</head>
<body>
  <main class="cover">
    <div class="brand">Brovantek</div>
    <h1 class="title">Catalogue</h1>

    <div class="product-visual" role="img" aria-label="Product group: pushbutton stations, emergency stop boxes, aluminium project boxes, mounting bracket and a clear-covered terminal block"></div>

    <section class="intro">
      <p>Arcimolupiet eatatemolore venes sint la voluptatiis as excest reri dusa ped maion expla core omnit at. It, ut rerundiasim int reped magnit, nam, qui oditium et voluptatur? Ant quodia doluptatur? Videl in era porpos est, con nonse nis mos el ma con nulla eat raecepelique omniaes ut alis estius. Tet qui audam quam quam facieni vel et et lam rero maxim ut enducil eseque et voluptatur acepe vent autati cuptas alisque qui dolorro coratur alitatatiur maiorpo resedis volorionsere sequis eum sita vollessum remquam reribus dolorate</p>
    </section>

    <ol class="index">
      <li><span>Terminal Enclosures</span><span>2</span></li>
      <li><span>Pushbutton Boxes</span><span>14</span></li>
      <li><span>Aluminum Project Boxes</span><span>26</span></li>
      <li><span>Accessories</span><span>45</span></li>
    </ol>
  </main>
</body>
</html>
```